Brightmill Data Works

Our company is about IT hardwares and IT solutions. IT hardware such as PC, RAMS, storage and servers. IT solutions such as project management, BA. We are also selling new technology too.

Target Market(s)

Consumer, Small to Medium Business, Corporate

Requirements
Must have
• The business card must have the following:
• Name:
• Title:
• Contact Number:
• Email address:
• Website:
• Color: Must match the logo color upgrade

```html
<!DOCTYPE html>
<html lang="en">
<head>
<meta charset="utf-8">
<title>Brightmill Data Works — Business Card</title>
<link rel="stylesheet" href="https://fonts.googleapis.com/css2?family=Lato:wght@400;700;900&display=swap">
<style>
  :root {
    --canvas: #3b3b3b;
    --ink: #1e1e1e;
    --charcoal: #464646;
    --card-dark: #121212;
    --card-dark-2: #1f1f1f;
    --paper: #ffffff;
    --amber: #e09a3a;
    --amber-deep: #d38a2a;
    --text: #2a2a2a;
  }
  * { box-sizing: border-box; margin: 0; padding: 0; }
  html, body {
    width: 1200px; height: 1200px; overflow: hidden;
    background: var(--canvas);
    font-family: "Lato", Arial, sans-serif;
  }
  .canvas {
    position: relative; width: 1200px; height: 1200px;
    background: radial-gradient(circle at 50% 40%, #4a4a4a 0%, var(--canvas) 70%);
  }
  .card {
    position: absolute; left: 110px; width: 980px; height: 560px;
    overflow: hidden;
  }
  /* Card face one: dark */
  .card--front { top: 30px; }
  .card__pattern {
    position: absolute; inset: 0;
    background: radial-gradient(circle at 50% 45%, var(--card-dark-2) 0%, var(--card-dark) 75%);
  }
  .front__brand {
    position: absolute; left: 0; right: 0; top: 220px;
    display: flex; align-items: center; justify-content: center; gap: 22px;
  }
  .brand-mark {
    width: 34px; height: 34px; background: var(--amber);
  }
  .brand-name {
    font-weight: 900; text-transform: uppercase; letter-spacing: 2px;
    font-size: 56px; line-height: 1;
  }
  .front__brand .brand-name { color: #ffffff; }
  .front__web {
    position: absolute; left: 0; right: 0; top: 400px;
    text-align: center; color: #ffffff; font-size: 26px; letter-spacing: 2px;
  }

  /* Card face two: white */
  .card--back { top: 610px; background: var(--paper); }
  .back__brand {
    position: absolute; left: 60px; top: 110px;
    display: flex; align-items: center; gap: 16px;
  }
  .back__brand .brand-mark { width: 26px; height: 26px; }
  .back__brand .brand-name { color: var(--charcoal); font-size: 40px; letter-spacing: 1px; }
  .person {
    position: absolute; right: 60px; top: 60px; text-align: right;
  }
  .person__name { color: var(--amber); font-weight: 700; font-size: 38px; }
  .person__title { color: var(--text); font-size: 24px; margin-top: 2px; }
  .rule {
    position: absolute; height: 2px; background: var(--amber);
  }
  .rule--top { left: 560px; right: 60px; top: 150px; }
  .rule--mid { left: 60px; right: 60px; top: 262px; }
  .address {
    position: absolute; right: 60px; top: 200px; text-align: right;
    color: var(--text); font-size: 26px; line-height: 1.25;
  }
  .contacts {
    position: absolute; left: 60px; top: 292px; list-style: none;
  }
  .contacts li {
    display: flex; align-items: center; gap: 18px;
    color: var(--text); font-size: 27px; line-height: 37px;
  }
  .contacts svg { width: 22px; height: 22px; fill: var(--amber); flex: none; }
  .band-dark {
    position: absolute; left: 0; bottom: 56px; width: 720px; height: 46px;
    background: var(--ink);
    clip-path: polygon(0 0, 100% 0, 96% 100%, 0 100%);
  }
  .band-web {
    position: absolute; right: 0; bottom: 80px; width: 380px; height: 56px;
    background: var(--amber);
    clip-path: polygon(5% 0, 100% 0, 100% 100%, 0 100%);
    display: flex; align-items: center; justify-content: flex-end; padding-right: 40px;
    color: #ffffff; font-size: 26px;
  }
</style>
</head>
<body>
<main class="canvas">

  <section class="card card--front" aria-label="Business card, front">
    <div class="card__pattern" role="img" aria-label="Faint repeating brand monogram pattern on black"></div>
    <div class="front__brand">
      <span class="brand-mark"></span>
      <span class="brand-name">Brightmill Data Works</span>
    </div>
    <p class="front__web">www.brightmilldata.com</p>
  </section>

  <section class="card card--back" aria-label="Business card, back">
    <div class="back__brand">
      <span class="brand-mark"></span>
      <span class="brand-name">Brightmill Data Works</span>
    </div>

    <div class="person">
      <p class="person__name">Daniel Hartley</p>
      <p class="person__title">Manager</p>
    </div>
    <div class="rule rule--top"></div>

    <p class="address">418 Alder Court<br>Austin, TX 78704</p>
    <div class="rule rule--mid"></div>

    <ul class="contacts">
      <li>
        <svg viewBox="0 0 24 24" aria-hidden="true"><path d="M6.6 10.8c1.4 2.8 3.8 5.1 6.6 6.6l2.2-2.2c.3-.3.7-.4 1-.2 1.1.4 2.3.6 3.6.6.6 0 1 .4 1 1V20c0 .6-.4 1-1 1C10.6 21 3 13.4 3 4c0-.6.4-1 1-1h3.5c.6 0 1 .4 1 1 0 1.3.2 2.5.6 3.6.1.3 0 .7-.2 1z"/></svg>
        555 014 2200
      </li>
      <li>
        <svg viewBox="0 0 24 24" aria-hidden="true"><path d="M6 2h12v5H6zM4 8h16a2 2 0 0 1 2 2v7h-4v5H6v-5H2v-7a2 2 0 0 1 2-2zm4 8v4h8v-4z"/></svg>
        555 014 2201
      </li>
      <li>
        <svg viewBox="0 0 24 24" aria-hidden="true"><path d="M2 5h20v14H2zm2 2v.4l8 5.2 8-5.2V7zm0 2.8V17h16V9.8l-8 5.2z"/></svg>
        info@brightmilldata.com
      </li>
    </ul>

    <div class="band-dark"></div>
    <div class="band-web">www.brightmilldata.com</div>
  </section>

</main>
</body>
</html>
```